Marrowind - IT Consultancy Website

Our company is called Marrowind and our purpose is to help companies sustainably embrace and reap the benefits of cloud platforms, through transforming practices, skills and technology using DevOps and Security practices such that they are able to automate, manage and secure their cloud platforms to deliver product to market with increasing velocity.

To get our business started I require a website that will model the typical layout of an IT consultancy services company to an Australian Market. There are many examples of such a site, here are some of them. We would like a landing page and then a few simple menu options (About, Blog, Services etc..) to additional content

http://pelvo.com.au/
http://www.brisket.com.au/
http://www.tandu.com.au/

I require the site to be created with a separate CSS file that maintains the colour palette. This is a very important requirement, I want to be able to change the colours employed in the site in a single location and not have to scan through multiple files to replace the codes.

The website must be built using static content as it will not be hosted on a web server but instead in QNT using S3 and CloudFront CDN. Therefore please stick to HTML, JavaScript, CSS and other static file formats. The website needs to be response, smooth and reactive. It should render on desktop, mobile and tablet and feature smooth scrolling, transitions and fade in's.

The website should give the customer confidence that they are dealing with a highly professional IT services company, focused strongly on cloud (QNT, Vantrel Skyline, Horvik Vapor etc..), motivated by beautiful and fluid design.

In order to make this simpler for you, the designer, I have already purchased this template from https://skinmarketly.com/theme/the-venture-allround-template-KX7Q41093 and uploaded it. Feel free to use this template if you choose (note that it makes use of a separate color palette which is a key requirement) or use one of your own choosing. If you do use this template ensure that it does not look too much like "another bootstrap site" therefore use the layout and widgets but make the site look fresh and original too.
Obviously you must delete all trace of the bootstrap package once the project has completed if you do use it

Target Market(s)

Corporate and medium enterprise businesses

Industry/Entity Type

Information Technology

Coding

Coded - Design and coding required

Number of Pages Required

4 page

Font styles to use
Sans Serif

Colors
abd036
33a6d7

Requirements
Must have
• The website should give the customer confidence that they are dealing with a highly professional IT services company, focused strongly on cloud (QNT, Vantrel Skyline, Horvik Vapor etc..), motivated by beautiful and fluid design. Our company name is Marrowind, the site needs to pay homage to the themes of fluidity and logic
• Along with About Us, Services and a Blog page could I also get social logo's included too
Nice to have
• The website must be built using static content as it will not be hosted on a web server but instead in QNT using S3 and CloudFront CDN. Therefore please stick to HTML, JavaScript, CSS and other static file formats. The website needs to be response, smooth and reactive. It should render on desktop, mobile and tablet and feature smooth scrolling, transitions and fade in's.
Should not have
• Lurid colours, or too much animations. The design must "flow"

```html
<!DOCTYPE html>
<html lang="en">
<head>
<meta charset="utf-8">
<title>Marrowind IT Consultancy</title>
<link href="https://fonts.googleapis.com/css2?family=Raleway:wght@400;500;600;700;800&family=Open+Sans:wght@400;600;700&display=swap" rel="stylesheet">
<style>
:root{
  --brand:#33a6d7;
  --brand-dark:#2390c0;
  --accent:#abd036;
  --ink:#2d2d2d;
  --text:#777;
  --muted:#999;
  --line:#e6e6e6;
  --white:#fff;
  --soft:#f4f5f6;
  --night:#262a2e;
  --deep:#1b1d20;
}
*{box-sizing:border-box;margin:0;padding:0}
html,body{width:1200px;height:3300px;overflow:hidden}
body{font-family:"Open Sans",Arial,sans-serif;color:var(--text);background:var(--white);font-size:13px;line-height:1.6;position:relative}
h1,h2,h3,h4,.nav,.btn{font-family:"Raleway",Arial,sans-serif}
.section{position:absolute;left:0;width:1200px}
.svg-ico{display:block}

/* top bar */
.topbar{top:0;height:48px;border-bottom:1px solid var(--line);display:flex;align-items:center;justify-content:space-between;padding:0 88px}
.social{display:flex;gap:6px}
.social span{width:24px;height:24px;border-radius:50%;background:var(--ink);display:block}
.topbar-contact{display:flex;gap:28px;font-size:12px;color:var(--ink)}
.topbar-contact span{display:flex;align-items:center;gap:6px}

/* header */
.header{top:48px;height:80px;display:flex;align-items:center;justify-content:space-between;padding:0 88px;box-shadow:0 2px 4px rgba(0,0,0,.06);z-index:2}
.logo{font-family:"Raleway",Arial,sans-serif;font-weight:800;font-size:24px;color:var(--ink);letter-spacing:.2px}
.logo .it{color:var(--brand)}
.logo .rest{font-weight:500}
.nav{display:flex;align-items:center;gap:30px;font-size:12px;font-weight:600;color:var(--ink);text-transform:uppercase}
.nav .search{width:34px;height:34px;border-radius:50%;background:var(--brand);display:flex;align-items:center;justify-content:center}

/* hero */
.hero{top:128px;height:500px;background:linear-gradient(120deg,#3d4b58 0%,#566370 40%,#2e3740 100%);text-align:center;color:var(--white)}
.hero::after{content:"";position:absolute;inset:0;background:rgba(20,25,30,.45)}
.hero-inner{position:relative;z-index:1;padding-top:180px}
.hero h1{font-size:40px;font-weight:700;letter-spacing:2px;text-transform:uppercase}
.hero h1 .it{color:var(--brand)}
.hero p{width:680px;margin:14px auto 26px;font-size:14px;color:#e5e5e5}
.btn{display:inline-block;font-size:12px;font-weight:700;text-transform:uppercase;letter-spacing:.5px;padding:10px 22px}
.btn-light{border:2px solid var(--white);color:var(--white)}
.btn-brand{background:var(--brand);color:var(--white)}
.hero-arrow{position:absolute;top:232px;z-index:1;width:40px;height:40px;border-radius:50%;background:rgba(0,0,0,.55);display:flex;align-items:center;justify-content:center}
.hero-arrow.prev{left:20px}.hero-arrow.next{right:20px}

/* section headings */
.sec-title{text-align:center;font-size:28px;font-weight:500;color:var(--ink);text-transform:uppercase;letter-spacing:1px}
.sec-title b{color:var(--brand);font-weight:700}
.sec-title::after{content:"";display:block;width:50px;height:2px;background:var(--brand);margin:10px auto 0}
.sec-lead{text-align:center;width:640px;margin:14px auto 0;font-size:13px}

/* services */
.services{top:628px;height:512px;background:var(--soft);padding-top:44px}
.cards{display:flex;gap:40px;padding:0 88px;margin-top:40px}
.card{width:312px;height:270px;background:var(--white);box-shadow:0 2px 8px rgba(0,0,0,.08);text-align:center;padding:32px 26px}
.card .icon{width:70px;height:70px;border-radius:50%;background:var(--brand);margin:0 auto 18px;display:flex;align-items:center;justify-content:center}
.card h3{font-size:20px;font-weight:500;color:var(--ink);margin-bottom:12px}
.card p{font-size:12px}
.card .more{display:block;margin-top:14px;color:var(--brand);font-size:12px;font-weight:600}

/* offer band */
.offer{top:1140px;height:132px;background:var(--brand);color:var(--white);display:flex;align-items:center;justify-content:space-between;padding:0 88px}
.offer h2{font-size:24px;font-weight:800;text-transform:uppercase}
.offer p{font-size:13px;width:700px;margin-top:4px;color:#e9f6fc}
.offer .btn{padding:12px 40px}

/* why */
.why{top:1272px;height:548px;padding-top:36px}
.why-body{display:flex;padding:0 88px 0 148px;margin-top:40px;gap:60px}
.why-text{width:380px;font-size:12px}
.checks{list-style:none;margin:18px 0 24px}
.checks li{display:flex;align-items:center;gap:10px;margin:8px 0}
.why-media{width:500px;height:300px;background:linear-gradient(180deg,#dfe3e7 0%,#f2f4f6 70%,#cfd4d9 100%);border-radius:4px}

/* projects */
.projects{top:1820px;height:390px;border-top:1px solid var(--line);padding-top:36px}
.gallery{display:flex;gap:8px;padding:0 88px;margin-top:32px}
.shot{width:248px;height:210px}
.shot.s1{background:linear-gradient(135deg,#c9d3dc,#8597a6)}
.shot.s2{background:linear-gradient(135deg,#b8a48e,#6f5a48)}
.shot.s3{background:linear-gradient(135deg,#a8b3bd,#4b5864)}
.shot.s4{background:linear-gradient(135deg,#d6cfc4,#8b7d6b)}

/* stats */
.stats{top:2210px;height:290px;background:linear-gradient(135deg,#33383e,#1f2327);display:flex;justify-content:space-around;padding:72px 120px 0}
.stat{text-align:center;color:var(--white);width:160px}
.stat .ring{width:100px;height:100px;border-radius:50%;background:rgba(255,255,255,.12);border:2px solid rgba(255,255,255,.35);margin:0 auto 14px;display:flex;align-items:center;justify-content:center}
.stat h4{font-size:15px;font-weight:700;letter-spacing:1px}
.stat span{font-size:14px}

/* partners */
.partners{top:2500px;height:120px;background:var(--deep);display:flex;align-items:center;justify-content:center;gap:130px}
.partner{display:flex;align-items:center;gap:12px;color:var(--white);font-family:"Raleway",Arial,sans-serif;font-size:26px;font-weight:600}
.partner i{width:26px;height:26px;background:var(--white);display:block}
.partner i.round{border-radius:50%}

/* testimonials */
.testimonials{top:2620px;height:340px;padding-top:34px;text-align:center}
.quote{position:relative;width:860px;margin:24px auto 0;font-size:13px;font-style:italic}
.quote .mark{position:absolute;top:-16px;font-size:36px;color:var(--ink);font-style:normal;font-family:Georgia,serif}
.quote .mark.l{left:-30px}.quote .mark.r{right:-30px}
.person{position:relative;width:400px;margin:22px auto 0;height:110px}
.person .curve{position:absolute;top:0;width:40px;height:70px;border:1px solid var(--line);border-radius:50%}
.person .curve.l{left:70px;border-right:none}.person .curve.r{right:70px;border-left:none}
.avatar{width:64px;height:64px;border-radius:50%;background:linear-gradient(135deg,#c7ced4,#7b8791);margin:0 auto}
.person h4{margin-top:8px;font-size:13px;color:var(--brand);font-weight:700}
.person small{font-size:11px;color:var(--muted)}

/* footer */
.footer{top:2960px;height:272px;background:var(--soft);display:flex;gap:50px;padding:36px 88px 0}
.col{width:220px}
.col h4{font-size:15px;font-weight:700;color:var(--ink);text-transform:uppercase;margin-bottom:14px}
.col p{font-size:12px}
.col .link{color:var(--brand);font-size:12px;font-weight:600;display:block;margin-top:10px}
.post{display:flex;gap:10px;margin-bottom:14px}
.post .thumb{width:60px;height:44px;background:linear-gradient(135deg,#9aa8b4,#56636e);flex:none}
.post b{display:block;font-size:12px;color:var(--ink);font-weight:600;line-height:1.4}
.post small{color:var(--brand);font-size:11px}
.contact-row{display:flex;gap:10px;align-items:center;font-size:12px;margin-bottom:8px}
.subscribe{display:flex;margin-bottom:14px}
.subscribe span{flex:1;height:32px;border:1px solid #d5d5d5;background:var(--white);font-size:11px;padding:6px 10px;color:var(--muted)}
.subscribe b{background:var(--brand);color:var(--white);font-size:11px;padding:7px 12px}
.footer .social span{background:var(--white);border:1px solid #ccc;width:28px;height:28px}

.bottom{top:3232px;height:68px;background:var(--night);color:#bbb;font-size:12px;display:flex;align-items:center;justify-content:center}
</style>
</head>
<body>

<div class="section topbar">
  <div class="social" aria-label="Social links"><span></span><span></span><span></span><span></span><span></span></div>
  <div class="topbar-contact">
    <span><svg width="12" height="12" viewBox="0 0 24 24"><path fill="#33a6d7" d="M6.6 10.8a15 15 0 0 0 6.6 6.6l2.2-2.2c.3-.3.7-.4 1-.2 1.1.4 2.3.6 3.6.6.6 0 1 .4 1 1V20c0 .6-.4 1-1 1A17 17 0 0 1 3 4c0-.6.4-1 1-1h3.5c.6 0 1 .4 1 1 0 1.3.2 2.5.6 3.6.1.3 0 .7-.2 1z"/></svg>+61 (02) 5550 1842</span>
    <span><svg width="13" height="11" viewBox="0 0 24 20"><rect x="1" y="1" width="22" height="18" rx="2" fill="none" stroke="#33a6d7" stroke-width="2"/><path d="M1 3l11 8 11-8" fill="none" stroke="#33a6d7" stroke-width="2"/></svg>Email: info@marrowind.com</span>
  </div>
</div>

<header class="section header">
  <div class="logo">Marrowind <span class="it">IT</span> <span class="rest">Consultancy</span></div>
  <nav class="nav">
    <span>Home</span><span>About Us</span><span>Services</span><span>Projects</span><span>News</span><span>Testimonials</span><span>Contact Us</span>
    <span class="search"><svg width="14" height="14" viewBox="0 0 24 24"><circle cx="10" cy="10" r="7" fill="none" stroke="#fff" stroke-width="3"/><path d="M15 15l7 7" stroke="#fff" stroke-width="3"/></svg></span>
  </nav>
</header>

<section class="section hero" role="img" aria-label="Photo of a business team meeting around a table">
  <div class="hero-inner">
    <h1>Marrowind <span class="it">IT</span> Consultancy</h1>
    <p>We help companies embrace the cloud with DevOps and security practices, so their teams can automate, manage and deliver product faster.</p>
    <span class="btn btn-light">Click here for more info</span>
  </div>
  <span class="hero-arrow prev"><svg width="12" height="16" viewBox="0 0 12 16"><path d="M9 2L3 8l6 6" fill="none" stroke="#fff" stroke-width="2.5"/></svg></span>
  <span class="hero-arrow next"><svg width="12" height="16" viewBox="0 0 12 16"><path d="M3 2l6 6-6 6" fill="none" stroke="#fff" stroke-width="2.5"/></svg></span>
</section>

<section class="section services">
  <h2 class="sec-title">Our <b>Services</b></h2>
  <p class="sec-lead">Practical cloud consulting for corporate and medium enterprise teams, from strategy and migration through to daily operations and security.</p>
  <div class="cards">
    <div class="card">
      <div class="icon"><svg width="34" height="24" viewBox="0 0 34 24"><path fill="#fff" d="M9 23a8 8 0 0 1-1-16 10 10 0 0 1 19 2 7 7 0 0 1-1 14z"/></svg></div>
      <h3>Cloud Platforms</h3>
      <p>Design, build and run secure cloud platforms that scale with your business and keep costs under clear control.</p>
      <span class="more">Read More »</span>
    </div>
    <div class="card">
      <div class="icon"><svg width="30" height="30" viewBox="0 0 24 24"><path fill="#fff" d="M19.4 13a7.5 7.5 0 0 0 0-2l2.1-1.6-2-3.5-2.5 1a7 7 0 0 0-1.7-1L15 3h-4l-.3 2.9a7 7 0 0 0-1.7 1l-2.5-1-2 3.5L6.6 11a7.5 7.5 0 0 0 0 2l-2.1 1.6 2 3.5 2.5-1a7 7 0 0 0 1.7 1L11 21h4l.3-2.9a7 7 0 0 0 1.7-1l2.5 1 2-3.5zM13 15.5a3.5 3.5 0 1 1 0-7 3.5 3.5 0 0 1 0 7z"/></svg></div>
      <h3>Transforming Practices</h3>
      <p>Introduce DevOps ways of working that help teams automate delivery and ship product with growing velocity.</p>
      <span class="more">Read More »</span>
    </div>
    <div class="card">
      <div class="icon"><svg width="24" height="32" viewBox="0 0 24 32"><path fill="#fff" d="M12 1a10 10 0 0 0-6 18c1 .8 1.5 2 1.5 3h9c0-1 .5-2.2 1.5-3A10 10 0 0 0 12 1zM8 25h8v2H8zm1 4h6v2H9z"/></svg></div>
      <h3>Skills &amp; Technology</h3>
      <p>Coaching and hands-on training that give your people the skills to manage and secure cloud tools with confidence.</p>
      <span class="more">Read More »</span>
    </div>
  </div>
</section>

<section class="section offer">
  <div>
    <h2>Don't miss out our offers</h2>
    <p>Book a free cloud readiness review this quarter and get a clear plan for your next steps in the cloud.</p>
  </div>
  <span class="btn btn-light">Learn More</span>
</section>

<section class="section why">
  <h2 class="sec-title">Why <b>Choose</b> Us</h2>
  <p class="sec-lead">We combine deep cloud knowledge with a calm, logical approach so change flows smoothly through your organisation.</p>
  <div class="why-body">
    <div class="why-text">
      <p>Our consultants have delivered cloud programs for Australian enterprises of every size. We focus on lasting results, not quick fixes, and leave your teams stronger than we found them.</p>
      <ul class="checks">
        <li><svg width="14" height="14" viewBox="0 0 14 14"><path d="M2 7l3 3 7-7" fill="none" stroke="#33a6d7" stroke-width="2.5"/></svg>Certified cloud architects on every team</li>
        <li><svg width="14" height="14" viewBox="0 0 14 14"><path d="M2 7l3 3 7-7" fill="none" stroke="#33a6d7" stroke-width="2.5"/></svg>Security built in from day one</li>
        <li><svg width="14" height="14" viewBox="0 0 14 14"><path d="M2 7l3 3 7-7" fill="none" stroke="#33a6d7" stroke-width="2.5"/></svg>Proven DevOps delivery methods</li>
        <li><svg width="14" height="14" viewBox="0 0 14 14"><path d="M2 7l3 3 7-7" fill="none" stroke="#33a6d7" stroke-width="2.5"/></svg>Clear pricing with no surprises</li>
        <li><svg width="14" height="14" viewBox="0 0 14 14"><path d="M2 7l3 3 7-7" fill="none" stroke="#33a6d7" stroke-width="2.5"/></svg>Local support across Australia</li>
        <li><svg width="14" height="14" viewBox="0 0 14 14"><path d="M2 7l3 3 7-7" fill="none" stroke="#33a6d7" stroke-width="2.5"/></svg>Skills transfer to your own people</li>
      </ul>
      <span class="btn btn-brand">Learn More</span>
    </div>
    <div class="why-media" role="img" aria-label="Desktop computer showing the website, with keyboard and mouse"></div>
  </div>
</section>

<section class="section projects">
  <h2 class="sec-title">Our <b>Projects</b></h2>
  <p class="sec-lead">A selection of recent engagements helping clients move, modernise and secure their cloud platforms.</p>
  <div class="gallery">
    <div class="shot s1" role="img" aria-label="Photo of colleagues working at a laptop"></div>
    <div class="shot s2" role="img" aria-label="Photo of a handshake across a desk"></div>
    <div class="shot s3" role="img" aria-label="Photo of a person typing on a laptop"></div>
    <div class="shot s4" role="img" aria-label="Photo of a team in a workshop"></div>
  </div>
</section>

<section class="section stats" role="img" aria-label="Dark photo of a desk with devices behind company figures">
  <div class="stat"><div class="ring"><svg width="36" height="32" viewBox="0 0 24 22"><path fill="#fff" d="M9 1h6a2 2 0 0 1 2 2v2h5a2 2 0 0 1 2 2v12a2 2 0 0 1-2 2H2a2 2 0 0 1-2-2V7a2 2 0 0 1 2-2h5V3a2 2 0 0 1 2-2zm0 2v2h6V3z"/></svg></div><h4>PROJECTS</h4><span>1325</span></div>
  <div class="stat"><div class="ring"><svg width="40" height="30" viewBox="0 0 30 22"><circle cx="15" cy="6" r="5" fill="#fff"/><path fill="#fff" d="M5 22c0-6 4-9 10-9s10 3 10 9z"/><circle cx="5" cy="8" r="3.5" fill="#fff"/><circle cx="25" cy="8" r="3.5" fill="#fff"/><path fill="#fff" d="M0 19c0-4 2-6 5-6 1 0 2 .2 2.5.6A11 11 0 0 0 4 19zm30 0c0-4-2-6-5-6-1 0-2 .2-2.5.6A11 11 0 0 1 26 19z"/></svg></div><h4>CLIENTS</h4><span>256</span></div>
  <div class="stat"><div class="ring"><svg width="32" height="32" viewBox="0 0 24 24"><path fill="#fff" d="M10 1h4v10h4l-6 7-6-7h4zM2 19h20v4H2z"/></svg></div><h4>DOWNLOADS</h4><span>1128</span></div>
  <div class="stat"><div class="ring"><svg width="32" height="32" viewBox="0 0 24 24"><circle cx="18" cy="5" r="3.5" fill="#fff"/><circle cx="6" cy="12" r="3.5" fill="#fff"/><circle cx="18" cy="19" r="3.5" fill="#fff"/><path d="M18 5L6 12l12 7" fill="none" stroke="#fff" stroke-width="2"/></svg></div><h4>SHARES</h4><span>12548</span></div>
</section>

<section class="section partners">
  <div class="partner"><i></i>QNT</div>
  <div class="partner"><i></i>Vantrel Skyline</div>
  <div class="partner"><i class="round"></i>Horvik Vapor</div>
</section>

<section class="section testimonials">
  <h2 class="sec-title">Our <b>Testimonials</b></h2>
  <div class="quote">
    <span class="mark l">“</span>
    <p>Marrowind guided our move to the cloud with patience and real expertise. Releases that once took weeks now take hours, and our team finally feels in control of the platform. We would recommend them to any business ready to grow.</p>
    <span class="mark r">”</span>
  </div>
  <div class="person">
    <span class="curve l"></span><span class="curve r"></span>
    <div class="avatar" role="img" aria-label="Client portrait"></div>
    <h4>Name – Ravi Tenning</h4>
    <small>Posted on 12 July 2016</small>
  </div>
</section>

<footer class="section footer">
  <div class="col">
    <h4>About Us</h4>
    <p>Marrowind is an Australian IT consultancy helping businesses adopt cloud platforms through better practices, skills and technology.</p>
    <span class="link">Read More »</span>
  </div>
  <div class="col">
    <h4>Latest Blog</h4>
    <div class="post"><div class="thumb" role="img" aria-label="Blog post photo"></div><div><b>Five steps to a secure cloud</b><small>Jul 02, 2016</small></div></div>
    <div class="post"><div class="thumb" role="img" aria-label="Blog post photo"></div><div><b>Why DevOps speeds delivery</b><small>Jun 18, 2016</small></div></div>
  </div>
  <div class="col">
    <h4>Contact Us</h4>
    <div class="contact-row"><svg width="12" height="12" viewBox="0 0 24 24"><path fill="#33a6d7" d="M6.6 10.8a15 15 0 0 0 6.6 6.6l2.2-2.2c.3-.3.7-.4 1-.2 1.1.4 2.3.6 3.6.6.6 0 1 .4 1 1V20c0 .6-.4 1-1 1A17 17 0 0 1 3 4c0-.6.4-1 1-1h3.5c.6 0 1 .4 1 1 0 1.3.2 2.5.6 3.6.1.3 0 .7-.2 1z"/></svg>+61 (02) 5550 1842</div>
    <div class="contact-row"><svg width="12" height="12" viewBox="0 0 24 24"><path fill="#33a6d7" d="M6.6 10.8a15 15 0 0 0 6.6 6.6l2.2-2.2c.3-.3.7-.4 1-.2 1.1.4 2.3.6 3.6.6.6 0 1 .4 1 1V20c0 .6-.4 1-1 1A17 17 0 0 1 3 4c0-.6.4-1 1-1h3.5c.6 0 1 .4 1 1 0 1.3.2 2.5.6 3.6.1.3 0 .7-.2 1z"/></svg>+61 (02) 5550 1843</div>
    <div class="contact-row"><svg width="13" height="11" viewBox="0 0 24 20"><rect x="1" y="1" width="22" height="18" rx="2" fill="none" stroke="#33a6d7" stroke-width="2"/><path d="M1 3l11 8 11-8" fill="none" stroke="#33a6d7" stroke-width="2"/></svg>info@marrowind.com</div>
    <div class="contact-row"><svg width="11" height="14" viewBox="0 0 20 26"><path fill="#33a6d7" d="M10 0a10 10 0 0 0-10 10c0 7 10 16 10 16s10-9 10-16A10 10 0 0 0 10 0zm0 14a4 4 0 1 1 0-8 4 4 0 0 1 0 8z"/></svg>12 Kellan Street, Sydney NSW</div>
  </div>
  <div class="col">
    <h4>Follow Us</h4>
    <div class="subscribe"><span>Enter email</span><b>SUBMIT</b></div>
    <div class="social" aria-label="Social links"><span></span><span></span><span></span><span></span><span></span></div>
  </div>
</footer>

<div class="section bottom">© Copyright 2016 Marrowind IT Consultancy. All Rights Reserved</div>

</body>
</html>
```